Garland Custom Boats Website update

I would like an updated website to my current site (Garlandboats.com).
I have an updated logo i would like to incorporate.
24 pages , would like to integrate videos of the boats (that i can upload later)

Target Market(s)

Professional and Commercial boat owners

Industry/Entity Type

Custom Boat Manufacturing

Coding

Coded - Design and coding required

Number of Pages Required

5+ page

Font styles to use
Serif

Requirements
Must have
• Easy to read, well laid-out, and video integration
Nice to have
• Fresh up to date look

```html
<!DOCTYPE html>
<html lang="en">
<head>
<meta charset="utf-8">
<title>Garland Custom Boats</title>
<link href="https://fonts.googleapis.com/css2?family=Roboto:ital,wght@0,400;0,500;0,700;0,900;1,900&family=Poppins:wght@400;500&display=swap" rel="stylesheet">
<style>
:root{
  --navy:#0b2a8f;
  --red:#b5121b;
  --ink:#1c1c1c;
  --text:#555;
  --mist:#e8eef8;
  --white:#fff;
  --black:#000;
  --orange:#e8792b;
}
*{margin:0;padding:0;box-sizing:border-box}
html,body{width:1200px;height:4518px;overflow:hidden}
body{font-family:"Roboto",sans-serif;color:var(--ink);background:var(--white);position:relative}
.abs{position:absolute}
.btn{position:absolute;display:flex;align-items:center;justify-content:center;gap:8px;background:var(--red);color:var(--white);font:700 13px "Roboto",sans-serif;border-radius:22px;text-transform:uppercase}
.btn .dot{width:12px;height:12px;border-radius:50%;background:var(--white);position:relative}
.btn .dot::after{content:"";position:absolute;left:4px;top:3px;border-left:5px solid var(--red);border-top:3px solid transparent;border-bottom:3px solid transparent}
.title{position:absolute;font:italic 900 34px/40px "Roboto",sans-serif;color:var(--ink);white-space:nowrap}
.title b{color:var(--navy);font-weight:900}
.title.center{left:0;width:1200px;text-align:center}
.topbar{left:695px;top:0;width:505px;height:36px;background:var(--navy);clip-path:polygon(20px 0,100% 0,100% 100%,0 100%);color:var(--white);font:500 13px "Roboto",sans-serif;display:flex;align-items:center;justify-content:flex-end;gap:44px;padding-right:113px}
.brand{font:700 22px/26px "Roboto",sans-serif;color:var(--navy);text-transform:uppercase}
.nav{left:455px;top:70px;display:flex;gap:24px;font:700 13px "Roboto",sans-serif;text-transform:uppercase}
.nav .on{color:var(--red)}
.hero{left:0;top:122px;width:1200px;height:570px}
.hero-h{left:110px;top:258px;font:italic 900 40px/55px "Roboto",sans-serif;color:var(--white);text-transform:uppercase}
.about-img{left:108px;top:805px;width:462px;height:478px;background:linear-gradient(135deg,#1f6fc4,#e57b2a 45%,#c9d5e0);border-radius:0 0 100px 0}
.about-frame{left:114px;top:811px;width:462px;height:478px;border:4px solid var(--red);border-left:none;border-top:none;border-radius:0 0 104px 0}
.about h3{left:640px;top:880px;font:700 20px/28px "Roboto",sans-serif;color:#3a3a3a;text-transform:uppercase;width:440px}
.about p{left:640px;width:445px;font:400 13px/26px "Poppins",sans-serif;color:var(--text)}
.mission{left:0;top:1366px;width:1200px;height:700px;background:linear-gradient(180deg,#dfe8f5,#eef2f9)}
.intro{left:0;width:1200px;text-align:center;font:400 13px/26px "Poppins",sans-serif;color:var(--text)}
.card-img{top:1603px;width:290px;height:236px;border-radius:60px 0 60px 0}
.card h4{top:1853px;width:290px;text-align:center;font:700 14px "Roboto",sans-serif;text-transform:uppercase}
.card p{top:1880px;width:290px;text-align:center;font:400 12px/23px "Poppins",sans-serif;color:var(--text)}
.arrow{position:absolute;width:40px;height:40px;border-radius:50%;display:flex;align-items:center;justify-content:center;font:700 16px "Roboto",sans-serif}
.arrow.l{background:var(--white);color:#333;box-shadow:0 2px 6px rgba(0,0,0,.15)}
.arrow.r{background:var(--navy);color:var(--white)}
.power{left:0;top:2066px;width:1200px;height:483px;background:var(--navy)}
.tab{position:absolute;top:2282px;width:156px;height:38px;border-radius:20px;display:flex;align-items:center;justify-content:center;font:700 13px "Roboto",sans-serif;color:var(--white)}
.badge{position:absolute;top:2372px;width:174px;height:80px;background:var(--white);border-radius:4px}
.badge i{position:absolute;left:40px;top:22px;width:94px;height:36px;background:#cfd6e6;border-radius:3px}
.t-card{left:185px;top:2740px;width:334px;height:266px;background:var(--white);border-radius:10px;box-shadow:0 6px 24px rgba(0,0,0,.12);padding:42px 22px}
.t-card h5{font:700 14px "Roboto",sans-serif}
.t-card .loc{font:400 13px "Poppins",sans-serif;color:var(--orange);margin:6px 0 18px}
.t-card p{font:400 11px/18px "Poppins",sans-serif;color:var(--text)}
.t-img{left:538px;top:2722px;width:478px;height:320px;background:linear-gradient(180deg,#c77c6a,#2c3a5c 55%,#1a2440);border-radius:4px}
.boat-band{left:0;top:3060px;width:1200px;height:450px;background:linear-gradient(180deg,#ffffff 0%,#d8e6f2 35%,#3f6f9e 70%,#163a66 100%)}
.gallery{left:0;top:3508px;width:1200px;height:600px;background:var(--mist)}
.g-item{position:absolute;top:3692px;width:458px;height:328px;border:5px solid var(--white);border-radius:8px;box-shadow:0 4px 16px rgba(0,0,0,.15)}
.play{position:absolute;left:50%;top:50%;width:74px;height:74px;margin:-37px 0 0 -37px;border-radius:50%;background:var(--white)}
.play::after{content:"";position:absolute;left:29px;top:22px;border-left:22px solid var(--navy);border-top:15px solid transparent;border-bottom:15px solid transparent}
.footer{left:0;top:4105px;width:1200px;height:413px}
.social{position:absolute;top:4345px;width:28px;height:28px;border-radius:50%;border:1px solid #555;background:#111}
.f-col{position:absolute;top:4220px;color:var(--white);font:400 13px/26px "Roboto",sans-serif}
.f-col h6{font:700 13px "Roboto",sans-serif;text-transform:uppercase;margin-bottom:12px}
.map{left:907px;top:4255px;width:180px;height:132px;background:linear-gradient(135deg,#e9e4dc,#d7dfe9);border-radius:4px}
</style>
</head>
<body>

<header>
  <div class="abs topbar"><span>&#9993;&nbsp; office@garlandboats.com</span><span>&#9742;&nbsp; (504) 555-0172</span></div>
  <div class="abs brand" style="left:108px;top:26px">Garland<br>Custom Boats</div>
  <nav class="abs nav"><span class="on">Home</span><span>About Us</span><span>Custom Boats</span><span>Design &amp; Build</span><span>Package</span></nav>
  <div class="btn" style="left:952px;top:58px;width:136px;height:42px">Contact Us</div>
</header>

<section class="abs hero">
  <svg width="1200" height="570" class="abs" style="left:0;top:0">
    <defs><linearGradient id="sea" x1="0" y1="0" x2="1" y2="1"><stop offset="0" stop-color="#0a1f4a"/><stop offset=".5" stop-color="#123f7c"/><stop offset="1" stop-color="#081a3e"/></linearGradient></defs>
    <path d="M0 0H1200V210C1150 420 1000 560 700 565H0Z" fill="var(--navy)"/>
    <path d="M0 0H1200V190C1140 400 990 550 700 555H0Z" fill="url(#sea)" role="img" aria-label="Photo of a white luxury yacht cutting through deep blue water"/>
  </svg>
</section>
<h1 class="abs hero-h">We don’t just build<br>boats .we craft dreams,<br>one hull at a time.</h1>
<div class="btn" style="left:111px;top:447px;width:226px;height:40px">Start Your Journey <span class="dot"></span></div>

<section class="about">
  <div class="abs about-frame"></div>
  <div class="abs about-img" role="img" aria-label="Photo of two boat builders in hard hats polishing a yacht hull"></div>
  <div class="title" style="left:640px;top:815px">ABOUT <b>US</b></div>
  <h3 class="abs">Crafting more than boats .we build dreams on water</h3>
  <p class="abs" style="top:948px">we are not just boat builders — we are artisans of heritage, passion, and precision. With generations of knowledge flowing through our hands, we specialize in creating custom wooden and fiber boats that echo tradition, strength, and elegance.</p>
  <p class="abs" style="top:1077px">Founded on the values of integrity, craftsmanship, and family legacy, every boat we build is a symbol of trust. From fishing boats to luxurious leisure crafts, we design with heart and deliver with care.</p>
  <div class="btn" style="left:641px;top:1179px;width:158px;height:40px">Learn More <span class="dot"></span></div>
</section>

<section>
  <div class="abs mission" role="img" aria-label="Faint harbour backdrop"></div>
  <div class="title center" style="top:1456px">BUILT FOR <b>EVERY MISSION</b></div>
  <p class="abs intro" style="top:1525px">We specialize in building custom fiberglass boats ranging from 28 to 72 feet, tailored to meet the unique<br>demands of diverse industries and marine applications. Our projects include:</p>
  <div class="arrow l" style="left:54px;top:1706px">‹</div>
  <div class="arrow r" style="left:1104px;top:1706px">›</div>
  <div class="card">
    <div class="abs card-img" style="left:116px;background:linear-gradient(180deg,#7fb4dd,#d65a2e 60%,#244a6a)" role="img" aria-label="Photo of an orange research vessel at port"></div>
    <h4 class="abs" style="left:116px">Research Vessels</h4>
    <p class="abs" style="left:116px">Designed for universities and scientific<br>missions with optional jib cranes, A-frames,<br>and lab-ready layouts</p>
  </div>
  <div class="card">
    <div class="abs card-img" style="left:456px;background:linear-gradient(180deg,#8a939c,#3b4550 55%,#12161c)" role="img" aria-label="Photo of a commercial dive boat on choppy water"></div>
    <h4 class="abs" style="left:456px">Commercial Dive Boats</h4>
    <p class="abs" style="left:456px">Optimized for safety, stability, and performance<br>in regional dive environments.</p>
  </div>
  <div class="card">
    <div class="abs card-img" style="left:796px;background:linear-gradient(180deg,#1d2430,#c9826a 50%,#2b3444)" role="img" aria-label="Photo of supply boats moored at sunset"></div>
    <h4 class="abs" style="left:796px">Supply Boats</h4>
    <p class="abs" style="left:796px">Durable, high-capacity crafts for efficient<br>transport in remote or offshore locations.</p>
  </div>
  <div class="btn" style="left:521px;top:1950px;width:158px;height:40px">Learn More <span class="dot"></span></div>
</section>

<section>
  <div class="abs power"></div>
  <div class="title center" style="top:2172px;color:#fff">POWER YOU CAN TRUST</div>
  <p class="abs intro" style="top:2241px;color:#fff">We offer both inboard and outboard engine configurations from trusted names in marine propulsion:</p>
  <div class="tab" style="left:437px;background:var(--red)">INBOARD</div>
  <div class="tab" style="left:606px;border:2px solid #fff">OUTBOARD</div>
  <div class="badge" style="left:290px"><i></i></div>
  <div class="badge" style="left:513px"><i></i></div>
  <div class="badge" style="left:736px"><i></i></div>
</section>

<section>
  <div class="title center" style="top:2627px">OUR <b>TESTIMONIALS</b></div>
  <div class="abs boat-band" role="img" aria-label="Photo of a center-console boat speeding across open water"></div>
  <div class="abs t-img" role="img" aria-label="Photo of a white yacht on calm water at dusk"></div>
  <div class="abs t-card">
    <h5>DANA WHITFIELD</h5>
    <div class="loc">Cape Girardeau, MO</div>
    <p>Lorem ipsum dolor sit amet, consectetur adipiscing elit, sed do eiusmod tempor incididunt ut labore et dolore magna aliqua. Ut enim ad minim veniam, quis nostrud exercitation ullamco laboris nisi ut aliquip ex ea commodo consequat. Duis aute irure dolor in reprehenderit in voluptate velit esse cillum dolore eu fugiat nulla pariatur.</p>
  </div>
  <div class="arrow l" style="left:106px;top:2853px">‹</div>
  <div class="arrow r" style="left:1052px;top:2853px">›</div>
</section>

<section>
  <div class="abs gallery"></div>
  <div class="title center" style="top:3605px">OUR <b>GALLERY</b></div>
  <div class="g-item" style="left:134px;background:linear-gradient(180deg,#5fa8de,#dfe7ee 55%,#c5543a 75%,#4b5b68)" role="img" aria-label="Video thumbnail of boats on trailers in a yard"><span class="play"></span></div>
  <div class="g-item" style="left:606px;background:linear-gradient(180deg,#9cc6e4,#2f6d96 55%,#163b5a)" role="img" aria-label="Video thumbnail of fishing trawlers at sea"><span class="play"></span></div>
  <div class="arrow l" style="left:106px;top:3846px">‹</div>
  <div class="arrow r" style="left:1052px;top:3846px">›</div>
</section>

<footer>
  <svg class="abs footer" width="1200" height="413">
    <path d="M0 413V230C60 80 240 10 520 0H1200V413Z" fill="var(--navy)"/>
    <path d="M14 413V240C80 95 250 18 540 10H1200V413Z" fill="var(--black)"/>
  </svg>
  <div class="abs brand" style="left:142px;top:4262px;color:#fff">Garland<br>Custom Boats</div>
  <span class="social" style="left:202px"></span>
  <span class="social" style="left:237px"></span>
  <span class="social" style="left:272px"></span>
  <div class="abs" style="left:157px;top:4388px;color:#fff;font:400 10px 'Roboto',sans-serif">Copyright@2025.All Rights Reserved</div>
  <div class="f-col" style="left:478px"><h6>Quick Links</h6>Home<br>About Us<br>Our Boats<br>Gallery<br>Contact us</div>
  <div class="f-col" style="left:658px"><h6>Contact Us</h6>Garland Boats, Inc.<br>4120 Harbor Rd.<br>Covington, LA 70433 USA<br>Fax:(504) 555-0188<br>Office:(504) 555-0172<br>Email:office@garlandboats.com</div>
  <div class="f-col" style="left:907px"><h6>Visit Us</h6></div>
  <div class="abs map" role="img" aria-label="Map showing the boatyard location"></div>
</footer>

</body>
</html>
```